Business Card for a mobile physiotherapy company

I need a layout for a business card for a mobile physiotherapy company.
Slogan is "Mobile Physiotherapy - Your Road To Recovery"
Phone number is 867-555-0142
Email VardenTherapy@postnest.ca (subject to change with website)
Website www.VardenTherapy.ca
My name and credentials: Luke Varden Luke Varden, BSc(kin), MPT, CAFCI, IMS
Information maybe included: Direct Billing, Services including Physiotherapy, IMS, acupuncture
Maybe include facebook and instagram logos
One side with the logo clean and sharp
Other side with details, try not to look too busy, keep everything concise

```html
<!DOCTYPE html>
<html lang="en">
<head>
<meta charset="utf-8">
<title>Varden Therapy – Business Card</title>
<link rel="stylesheet" href="https://fonts.googleapis.com/css2?family=Crimson+Pro:wght@400;700&display=swap">
<style>
  :root {
    --backdrop: #c9c9c9;
    --navy: #27466e;
    --navy-deep: #223f66;
    --teal: #1d5a52;
    --paper: #f1f1f1;
    --ink-light: #ffffff;
    --ink-soft: #e4e9ee;
    --brand-ink: #2a4169;
  }
  * { box-sizing: border-box; margin: 0; padding: 0; }
  html, body { width: 1200px; height: 576px; overflow: hidden; }
  body {
    background: var(--backdrop);
    font-family: "Crimson Pro", Georgia, serif;
    position: relative;
  }
  .card {
    position: absolute;
    top: 138px;
    width: 484px;
    height: 293px;
    border-radius: 13px;
    overflow: hidden;
  }

  /* Front */
  .card--front {
    left: 82px;
    background: linear-gradient(20deg, var(--teal) 0%, #22506a 45%, var(--navy) 100%);
    color: var(--ink-light);
    text-align: center;
  }
  .front__brand {
    position: absolute;
    left: 0; right: 0;
    top: 112px;
    font-size: 42px;
    font-weight: 700;
    line-height: 1;
    color: var(--ink-light);
  }
  .front__tagline {
    position: absolute;
    left: 0; right: 0; top: 164px;
    font-size: 15px;
    color: var(--ink-soft);
  }
  .front__services {
    position: absolute;
    left: 0; right: 0; bottom: 18px;
    font-size: 16px;
    color: var(--ink-soft);
  }

  /* Back */
  .card--back {
    left: 602px;
    background: var(--paper);
  }
  .back__panel { position: absolute; inset: 0; }
  .back__brand {
    position: absolute;
    left: 10px; width: 204px;
    top: 131px;
    text-align: center;
    font-size: 29px;
    font-weight: 700;
    line-height: 1;
    color: var(--brand-ink);
  }
  .contact {
    position: absolute;
    left: 270px; top: 48px;
    color: var(--ink-light);
  }
  .contact__name { font-size: 24px; font-weight: 700; letter-spacing: 0.5px; line-height: 1; }
  .contact__creds { font-size: 14px; line-height: 17px; color: var(--ink-soft); margin-top: 8px; }
  .contact__follow {
    display: flex; align-items: center; gap: 6px;
    font-size: 16px; line-height: 20px; margin-top: 16px;
  }
  .social-dot { width: 19px; height: 19px; border-radius: 50%; background: var(--ink-soft); }
  .contact__list { list-style: none; margin-top: 7px; }
  .contact__list li {
    display: flex; align-items: center; gap: 11px;
    font-size: 16px; line-height: 18px;
  }
  .contact__list svg { width: 11px; height: 11px; fill: var(--ink-soft); flex: none; }
  .contact__tagline { font-size: 16px; line-height: 18px; margin-top: 16px; color: var(--ink-soft); }
</style>
</head>
<body>
  <section class="card card--front" aria-label="Card front">
    <p class="front__brand">Varden Therapy</p>
    <p class="front__tagline">Mobile Physiotherapy - Your Road To Recovery</p>
    <p class="front__services">Direct Billing &nbsp;|&nbsp; Services Including Physiotherapy &nbsp;|&nbsp; IMS &nbsp;|&nbsp; Acupuncture</p>
  </section>

  <section class="card card--back" aria-label="Card back">
    <svg class="back__panel" viewBox="0 0 484 293" preserveAspectRatio="none">
      <defs>
        <linearGradient id="panelGradient" x1="0" y1="0" x2="0" y2="1">
          <stop offset="0" stop-color="#27466e"/>
          <stop offset="0.55" stop-color="#244d68"/>
          <stop offset="1" stop-color="#1d5a52"/>
        </linearGradient>
      </defs>
      <path d="M198,0 Q270,146 198,293 L484,293 L484,0 Z" fill="url(#panelGradient)"/>
      <path d="M198,0 Q262,146 198,293 L205,293 Q274,146 205,0 Z" fill="#223f66"/>
    </svg>
    <p class="back__brand">Varden Therapy</p>
    <div class="contact">
      <h1 class="contact__name">LUKE VARDEN</h1>
      <p class="contact__creds">BSc(kin), MPT, CAFCI, IMS</p>
      <p class="contact__follow">Follow us on: <span class="social-dot"></span><span class="social-dot"></span></p>
      <ul class="contact__list">
        <li><svg viewBox="0 0 10 10"><path d="M1 3 Q5 0 9 3 L8 4.5 L6.5 3.8 L6.5 3 Q5 2.6 3.5 3 L3.5 3.8 L2 4.5 Z M2.5 5 L7.5 5 L8.5 9 L1.5 9 Z"/></svg>867-555-0142</li>
        <li><svg viewBox="0 0 10 10"><path d="M0 2 L10 2 L10 8 L0 8 Z M0.8 2.6 L5 5.6 L9.2 2.6 L9.2 3.4 L5 6.4 L0.8 3.4 Z" fill-rule="evenodd"/></svg>VardenTherapy@postnest.ca</li>
        <li><svg viewBox="0 0 10 10"><circle cx="5" cy="5" r="4.4" fill="none" stroke="#e4e9ee" stroke-width="0.9"/><ellipse cx="5" cy="5" rx="1.8" ry="4.4" fill="none" stroke="#e4e9ee" stroke-width="0.8"/><path d="M0.6 5 H9.4" stroke="#e4e9ee" stroke-width="0.8"/></svg>www.VardenTherapy.ca</li>
      </ul>
      <p class="contact__tagline">Mobile Physiotherapy<br>Your Road To Recovery</p>
    </div>
  </section>
</body>
</html>
```